movie poster Dustwhisper

Create a movie poster for a thriller/suspense/horror movie called Dustwhisper which is about a monastery of sinister monks who are hell bent on destroying the world when three friends come on a photography assignment and find they may never escape!

A Marlene Hobart Film

Luke Penrose -- Owen
Danielle Forde -- Nora
Howard Pike -- Felix
Dale Ruddock --- Brother Lorenzo
Thaddeus Hobart -- Brother Benedetto
Norman Ellery ---Father Ignacio
Benjamin Holt -- Cardinal Vescovini
with Warren Tesky --- Gas Station Attendant

Marlene Hobart -- Writer, Director, Producer
Stephen Pike -- Director of Photography
Howard Pike -- Special Effects
Stephen Pike -- Editor
Lonnie "Buzzy" Marquez -- Sound

I just posted an update on the brief for the poster. Please include the credits on your movie poster. Thanks! I will be making a selection in the next few days.

Target Market(s)

This will be a PG and should attract a wide audience

Industry/Entity Type

Movie

Colors
eb1f27

Requirements
Must have
• Movie title, movie credits as provided
All material must be original --- no clip art or material taken from the internet
Nice to have
• tagline
Seeing is believing . . . until you believe what you don't see.

```html
<!DOCTYPE html>
<html lang="en">
<head>
<meta charset="utf-8">
<title>Dustwhisper — Movie Poster</title>
<link rel="stylesheet" href="https://fonts.googleapis.com/css2?family=Cinzel:wght@400;500&display=swap">
<style>
  :root {
    --backdrop: #e9e9e7;
    --paper: #ffffff;
    --blood: #eb1f27;
    --blood-deep: #8e0c12;
    --void: #120203;
    --title-ink: #ffffff;
    --credit-ink: #2a2a2a;
  }
  * { margin: 0; padding: 0; box-sizing: border-box; }
  html, body {
    width: 1200px;
    height: 1148px;
    overflow: hidden;
    background: var(--backdrop);
  }
  .stage {
    width: 1200px;
    height: 1148px;
    display: flex;
    align-items: center;
    justify-content: center;
  }
  .poster {
    width: 790px;
    height: 1100px;
    background: var(--paper);
    box-shadow: 0 2px 14px rgba(0,0,0,0.12);
  }
  .poster svg { display: block; width: 100%; height: 100%; }
  .movie-title {
    font-family: "Cinzel", "Times New Roman", serif;
    font-weight: 400;
    fill: var(--title-ink);
  }
  .presenter, .tagline, .credits {
    font-family: "Cinzel", "Times New Roman", serif;
  }
  .presenter { font-size: 15px; fill: var(--credit-ink); letter-spacing: 3px; }
  .tagline { font-size: 15px; fill: var(--blood); letter-spacing: 1px; }
  .credits { font-size: 11px; fill: var(--credit-ink); letter-spacing: 0.5px; }
  .credits .credits-head { font-weight: 500; fill: var(--blood); }
</style>
</head>
<body>
<main class="stage">
  <section class="poster" aria-label="Dustwhisper movie poster">
    <svg viewBox="0 0 790 1100" xmlns="http://www.w3.org/2000/svg">
      <defs>
        <radialGradient id="marble-red" cx="45%" cy="50%" r="70%">
          <stop offset="0" stop-color="var(--blood)"/>
          <stop offset="0.45" stop-color="var(--blood-deep)"/>
          <stop offset="1" stop-color="var(--void)"/>
        </radialGradient>
        <linearGradient id="flourish-tone" x1="0" y1="0" x2="1" y2="1">
          <stop offset="0" stop-color="#ffffff"/>
          <stop offset="1" stop-color="#f3d6d7"/>
        </linearGradient>
      </defs>

      <path class="texture-field" role="img"
            aria-label="Dark red and black swirling smoke texture"
            fill="url(#marble-red)"
            d="M560 40 C620 18 700 8 790 28 L790 380
               C760 400 745 440 735 480
               C720 540 700 600 690 640
               C670 700 640 760 600 800
               C540 860 460 900 400 960
               C370 1000 345 1050 330 1100
               L0 1100 L0 690
               C110 640 190 580 250 470
               C290 400 350 370 385 330
               C440 260 520 190 555 130
               C575 95 565 65 560 40 Z"/>

      <g class="scallops" fill="var(--paper)">
        <circle cx="770" cy="445" r="28"/>
        <circle cx="745" cy="520" r="22"/>
        <circle cx="720" cy="600" r="26"/>
        <circle cx="680" cy="700" r="30"/>
        <circle cx="610" cy="800" r="34"/>
        <circle cx="530" cy="870" r="28"/>
        <circle cx="450" cy="935" r="24"/>
        <circle cx="395" cy="1000" r="20"/>
      </g>

      <g class="flourish" role="img" aria-label="White calligraphic flourish ornament">
        <ellipse cx="560" cy="740" rx="120" ry="60" transform="rotate(-50 560 740)"
                 fill="url(#flourish-tone)" opacity="0.35"/>
      </g>

      <text class="movie-title" x="0" y="0" font-size="100"
            textLength="1000" lengthAdjust="spacing"
            transform="translate(85 960) rotate(-50)">DUSTWHISPER</text>

      <text class="presenter" x="40" y="60">A Marlene Hobart Film</text>
      <text class="tagline" x="40" y="100">
        <tspan x="40">Seeing is believing . . .</tspan>
        <tspan x="40" dy="22">until you believe what you don't see.</tspan>
      </text>

      <text class="credits" text-anchor="end">
        <tspan class="credits-head" x="765" y="900">Starring</tspan>
        <tspan x="765" dy="14">Luke Penrose — Owen</tspan>
        <tspan x="765" dy="14">Danielle Forde — Nora</tspan>
        <tspan x="765" dy="14">Howard Pike — Felix</tspan>
        <tspan x="765" dy="14">Dale Ruddock — Brother Lorenzo</tspan>
        <tspan x="765" dy="14">Thaddeus Hobart — Brother Benedetto</tspan>
        <tspan x="765" dy="14">Norman Ellery — Father Ignacio</tspan>
        <tspan x="765" dy="14">Benjamin Holt — Cardinal Vescovini</tspan>
        <tspan x="765" dy="14">with Warren Tesky — Gas Station Attendant</tspan>
        <tspan x="765" dy="18">Marlene Hobart — Writer, Director, Producer</tspan>
        <tspan x="765" dy="14">Stephen Pike — Director of Photography, Editor</tspan>
        <tspan x="765" dy="14">Howard Pike — Special Effects</tspan>
        <tspan x="765" dy="14">Lonnie "Buzzy" Marquez — Sound</tspan>
      </text>
    </svg>
  </section>
</main>
</body>
</html>
```